I would like some help creating my first business cards for my new business, I am a facilitator of a course that I have created. I am currently starting the sales promotion and marketing part of my business and need some help designing the business cards. Something fairly simple would be good, the core theme of my work is in connection of women to themselves and to each other. My initial design is a tree lit up by lights, a very mother earth type of image. This is not my design however so I probably am not legally able to use the design. I don't have a logo. Could you possibly assist with this?

I would really like to have the following details on the business card:
Meg Donlan
0431 582 917
hi.meg.donlan@larkmail.example

And also the image

Target Market(s)

Women who are living in an isolated environment

Industry/Entity Type

Counsellor

Contact Information for Business Card

Meg Donlan
Facilitator
hi.meg.donlan@larkmail.example
0431 582 917

Font styles to use
Other font styles liked:
• Handwriting - Dakota

Colors
e34197
fee18a
3276b5
33a6d7
33b8a4

Requirements
Must have
• 1) My details as above
• 2) a design (picture) that represents the mother earth theme similar to the designs included in the brief
• 3) no copyright attached to the design
• 4) Colours are very important but it is difficult to describe the colour using the colour wheel. Please refer to the example of the tree that I have included in the drop box.
• 5) I must apologise that I forgot to add the business card needs to have the name of the business in gold letters please: Riverbend Circle Gatherings Collective, thank you
Nice to have
• It would be great to use the tree design that I included in the brief, this is my favourite picture but I think it is probably copyrighted. If it's not, that is the one I would like on my business cards please.

```html
<!DOCTYPE html>
<html lang="en">
<head>
<meta charset="utf-8">
<title>Riverbend Circle Gatherings Collective – Business Card</title>
<link href="https://fonts.googleapis.com/css2?family=Great+Vibes&family=Open+Sans:wght@400;700&display=swap" rel="stylesheet">
<style>
  :root {
    --page-bg: #e9eef3;
    --sky-top: #a9d6f2;
    --sky-glow: #ffffff;
    --sky-edge: #9fd0ee;
    --earth: #5e4122;
    --title-gold: #b8892a;
    --name-brown: #5a3a17;
    --role-grey: #6b6b6b;
    --contact-brown: #4a3420;
    --tree-warm: #f4a93b;
    --tree-cool: #b7d98c;
  }
  * { margin: 0; padding: 0; box-sizing: border-box; }
  html, body {
    width: 1200px; height: 898px; overflow: hidden;
    background: var(--page-bg);
  }
  .card {
    position: absolute; left: 100px; top: 163px;
    width: 1000px; height: 571px; overflow: hidden;
    background:
      radial-gradient(ellipse 420px 300px at 62% 45%, var(--sky-glow) 0%, rgba(255,255,255,0) 100%),
      linear-gradient(160deg, var(--sky-top), var(--sky-edge));
    box-shadow: 0 10px 30px rgba(40, 60, 80, 0.25);
  }
  .identity {
    position: absolute; right: 120px; top: 34px; text-align: right;
    font-family: "Open Sans", sans-serif;
  }
  .identity__name { font-weight: 700; font-size: 27px; color: var(--name-brown); line-height: 1.1; }
  .identity__role { font-size: 17px; color: var(--role-grey); }
  .business-name {
    position: absolute; left: 520px; top: 112px; width: 440px;
    font-family: "Great Vibes", cursive; font-size: 60px; line-height: 1.05;
    color: var(--title-gold); text-align: center;
  }
  .tree-art {
    position: absolute; left: 40px; top: 130px; width: 440px; height: 340px;
    border-radius: 50% 50% 40% 40%;
    background: radial-gradient(ellipse at 50% 45%, var(--tree-warm) 0%, rgba(183,217,140,0.7) 45%, rgba(183,217,140,0) 72%);
  }
  .ground { position: absolute; left: 0; top: 0; width: 1000px; height: 571px; }
  .contacts {
    position: absolute; left: 440px; top: 392px;
    display: flex; gap: 24px; align-items: center; white-space: nowrap;
    font-family: "Open Sans", sans-serif; font-size: 19px; color: var(--contact-brown);
  }
  .contact { display: flex; align-items: center; gap: 8px; white-space: nowrap; }
  .contact svg { width: 22px; height: 22px; flex: none; }
</style>
</head>
<body>
  <div class="card">
    <div class="tree-art" role="img" aria-label="Illustration of a tree with a canopy of colourful circles and flowers"></div>

    <svg class="ground" viewBox="0 0 1000 571" aria-hidden="true">
      <path d="M0 515 C 300 505, 650 478, 1000 440 L1000 571 L0 571 Z" fill="var(--earth)"/>
    </svg>

    <div class="identity">
      <div class="identity__name">Meg Donlan</div>
      <div class="identity__role">Facilitator</div>
    </div>

    <div class="business-name">Riverbend Circle<br>Gatherings<br>Collective</div>

    <div class="contacts">
      <div class="contact">
        <svg viewBox="0 0 24 24" aria-hidden="true"><circle cx="12" cy="12" r="11" fill="var(--contact-brown)"/><path d="M7 10c0-2 2-3 5-3s5 1 5 3l-2 1-1-2h-4l-1 2zM8 12h8l1 5H7z" fill="#fff"/></svg>
        <span>0431 582 917</span>
      </div>
      <div class="contact">
        <svg viewBox="0 0 24 24" aria-hidden="true"><circle cx="12" cy="12" r="11" fill="var(--contact-brown)"/><rect x="6" y="8" width="12" height="8" fill="#fff"/><path d="M6 8l6 5 6-5" fill="none" stroke="var(--contact-brown)" stroke-width="1.3"/></svg>
        <span>hi.meg.donlan@larkmail.example</span>
      </div>
    </div>
  </div>
</body>
</html>
```